Sales and Marketing company needs website page graphics

We are redesigning our website and need graphics for the top of our solution pages. Currently you’ll see that there is one photo graphic with a differing color screen for each section. We’re looking for photo graphic designs that will represent each unique solution section (lead generation, prospecting, hiring) and fit within the overall website design. We will add the section title text to the photo graphic. This will be a total of 3 graphics.

This is a link to the working website redesign: http://trevindale.com/brunexatemp/
The content on the working redesign page is correct and will give you a good sense for how we talk about each solution. You’ll notice that the redesign is text heavy. We’ll work on that next.

Our current website is: www.brunexa.com
You’ll get a good sense for our designs on our blog: http://www.brunexa.com/blog

As a company, our goal is to help our clients get more customers. We do that through consulting, training and outsourced lead generation. Key words that describe us: flexible, responsive, and fun. (Although you don’t see that in our current website, hopefully it comes through more on our blog – and then on our new website!)

We will need the graphic design in high resolution formats. We will own the copyright and intellectual property.

North American companies that earn $750K - $85M in annual revenue selling to other businesses. Most are in the computer technology industry.

Business Service

Sans Serif

• Fit the design of the website.
• If there are people in the graphics, I like to see diversity: Asian,Black, Latin, Caucasian, men and women.
• Be creative, not like every other graphic you see on a website. We are a woman owned business and Marisol is well known. We don't want to feel generic. Potentially be something we can use elements of for other graphics.
• We really want your expertise and this is our first project with Artvoyle .
• We will insert the solution section text, so there wouldn't be the text unless it's part of the graphic design.

```html
<!DOCTYPE html>
<html lang="en">
<head>
<meta charset="utf-8">
<title>Brunexa Group – Sales Prospecting</title>
<link href="https://fonts.googleapis.com/css2?family=Lato:wght@400;700&display=swap" rel="stylesheet">
<style>
  :root {
    --purple: #5e3a8f;
    --purple-deep: #4b2a78;
    --purple-text: #6a3fa0;
    --green: #7fbf3f;
    --grey: #9a9a9a;
    --grey-light: #c9c9c9;
    --ink: #333333;
    --paper: #ffffff;
    --hero-light: #ecebf2;
    --hero-mid: #b9b3cc;
    --hero-dark: #4a3a6e;
  }
  * { box-sizing: border-box; margin: 0; padding: 0; }
  html, body {
    width: 1200px; height: 758px; overflow: hidden;
    background: var(--paper);
    font-family: "Lato", Arial, sans-serif;
    color: var(--ink);
  }
  .page {
    width: 1200px; height: 758px;
    background: var(--paper);
    overflow: hidden;
    position: relative;
  }
  .site-header {
    height: 68px;
    position: relative;
  }
  .brand {
    position: absolute; left: 90px; top: 18px;
    display: flex; align-items: center; gap: 10px;
    font-weight: 700; font-size: 28px; color: var(--purple-deep);
  }
  .brand-mark { width: 14px; height: 14px; background: var(--purple-deep); }
  .speak-link {
    position: absolute; left: 800px; top: 34px;
    font-size: 12px; font-weight: 700; letter-spacing: .04em;
    color: var(--purple-text); text-transform: uppercase;
  }
  .phone {
    position: absolute; right: 30px; top: 14px;
    font-size: 20px; color: var(--purple-text);
  }
  .main-nav {
    height: 30px; background: var(--purple);
    display: flex; justify-content: flex-end; align-items: stretch;
    padding-right: 30px;
  }
  .main-nav a {
    color: var(--paper); text-decoration: none;
    font-size: 11px; font-weight: 700; text-transform: uppercase;
    display: flex; align-items: center; padding: 0 11px;
  }
  .main-nav a.is-current { background: var(--green); }
  .hero {
    height: 300px;
    background:
      radial-gradient(ellipse 38% 60% at 52% 42%, var(--hero-light) 0%, rgba(236,235,242,0) 100%),
      linear-gradient(160deg, var(--hero-mid) 0%, #d9d6e4 40%, var(--hero-mid) 70%, var(--hero-dark) 100%);
  }
  .intro {
    display: flex; gap: 24px;
    padding: 22px 110px 0 250px;
  }
  .system-diagram { flex: 0 0 200px; }
  .intro-copy { flex: 1; font-size: 12px; line-height: 1.6; }
  .intro-copy h1 {
    font-size: 30px; font-weight: 400; color: var(--purple-text);
    margin-bottom: 8px; white-space: nowrap;
  }
  .intro-copy p { margin-bottom: 10px; }
  .intro-copy ul { margin: 0 0 10px 22px; }
  .intro-copy a { color: var(--purple-text); text-decoration: none; font-weight: 700; }
</style>
</head>
<body>
<div class="page">
  <header class="site-header">
    <div class="brand"><span class="brand-mark"></span>Brunexa Group</div>
    <span class="speak-link">Hire Marisol to speak</span>
    <span class="phone">+1 555 014 2290</span>
  </header>

  <nav class="main-nav">
    <a href="#">About</a>
    <a href="#">What we do</a>
    <a href="#">Lead generation</a>
    <a href="#" class="is-current">Prospecting</a>
    <a href="#">Hiring &amp; onboarding</a>
    <a href="#">Resources</a>
    <a href="#">Events</a>
    <a href="#">Blog</a>
    <a href="#">Contact</a>
  </nav>

  <div class="hero" role="img" aria-label="Section photo graphic: close-up of lavender-toned keyboard keys with a shopping cart key in focus"></div>

  <section class="intro">
    <svg class="system-diagram" width="200" height="200" viewBox="0 0 200 200" aria-label="Revenue Generating System diagram">
      <circle cx="100" cy="108" r="68" fill="none" stroke="var(--grey-light)" stroke-width="6"/>
      <text x="100" y="100" text-anchor="middle" font-family="Lato, sans-serif" font-size="15" fill="var(--grey)">Revenue</text>
      <text x="100" y="117" text-anchor="middle" font-family="Lato, sans-serif" font-size="15" fill="var(--grey)">Generating</text>
      <text x="100" y="134" text-anchor="middle" font-family="Lato, sans-serif" font-size="15" fill="var(--grey)">System</text>
      <circle cx="100" cy="36" r="28" fill="var(--grey)" stroke="#fff" stroke-width="3"/>
      <text x="100" y="33" text-anchor="middle" font-family="Lato, sans-serif" font-size="7" font-weight="700" fill="#fff">LEAD</text>
      <text x="100" y="43" text-anchor="middle" font-family="Lato, sans-serif" font-size="7" font-weight="700" fill="#fff">GENERATION</text>
      <circle cx="40" cy="150" r="30" fill="var(--purple)" stroke="#fff" stroke-width="3"/>
      <text x="40" y="153" text-anchor="middle" font-family="Lato, sans-serif" font-size="7" font-weight="700" fill="#fff">PROSPECTING</text>
      <circle cx="160" cy="150" r="28" fill="var(--grey)" stroke="#fff" stroke-width="3"/>
      <text x="160" y="148" text-anchor="middle" font-family="Lato, sans-serif" font-size="7" font-weight="700" fill="#fff">HIRING &amp;</text>
      <text x="160" y="158" text-anchor="middle" font-family="Lato, sans-serif" font-size="7" font-weight="700" fill="#fff">ONBOARDING</text>
    </svg>

    <div class="intro-copy">
      <h1>The Brunexa Group Approach to Sales Prospecting</h1>
      <p>Sales is not an art. We believe that sales is a skill that can be learned. It's a matter of giving sales people:</p>
      <ul>
        <li>The right tools,</li>
        <li>The right approach, and</li>
        <li>The right sales training</li>
      </ul>
      <p>All to develop the right sales skills to build their sales confidence. Each sales prospecting program at Brunexa Group integrates these crucial three components to build sales confidence and get more customers.</p>
      <p>Many business owners and sales managers consider cold calling to be the only effective prospecting strategy for new business development. The truth is that cold calling is only one new business development strategy. The best sales prospecting strategy combines a <a href="#">mix of prospect attraction strategies</a>: personal, digital, and collaborative.</p>
      <p>Sales people cannot rely on just one approach to effectively connect with contacts. Cold calling, emailing and social</p>
    </div>
  </section>
</div>
</body>
</html>
```